Heron Property Inspection business card

I am the principal inspector of Heron Property Inspections. I serve Northern Virginia from Winchester to Arlington.Associate, Federated Guild of Dwelling Examiners (FGDE)Graduate, FGDE Home Inspectors CourseNational Association of Home Inspectors ExamI'd like the business card to look more professional than comical.I pulled the attached picture off the web. I'd like to have something like that or an image of a house as my logo on the cards.

Target Market(s)

Persons who recently purchased a home.

Industry/Entity Type

Business

Contact Information for Business Card

Bob AllenBadger Home Inspections, LLC.4455 River RoadBluemont, Virginia 20135cell: 703-231-6680e-mail: tkmarlow@postvale.net

Font styles to use
Serif
Sans Serif

Requirements
Must have
• I'd like to have a logo, something that identifies me as a home inspector. The attached images are something that I'd like to have incorporated into my business card logo.
Nice to have
• I'd like a sketch of a house and/or a magnifying glass showing a house being inspected. The attached images are used as a suggestion only, I do not own the images.
Should not have
• Gimmicky stuff. I want to appear professional and trustworthy.

```html
<!DOCTYPE html>
<html lang="en">
<head>
<meta charset="utf-8">
<title>Heron Property Inspections – Business Card</title>
<link rel="stylesheet" href="https://fonts.googleapis.com/css2?family=Exo+2:wght@400;500;700&display=swap">
<style>
  :root {
    --stage: #e7e9ed;
    --card: #ffffff;
    --navy: #1f3d7f;
    --sky: #1b9bc9;
    --ink: #3d3f44;
    --muted: #4a4c52;
  }
  * { margin: 0; padding: 0; box-sizing: border-box; }
  html, body {
    width: 1200px; height: 902px; overflow: hidden;
    background: var(--stage);
    font-family: "Exo 2", sans-serif;
  }
  .card {
    position: absolute; left: 50px; top: 138px;
    width: 1100px; height: 626px;
    background: var(--card);
    overflow: hidden;
    box-shadow: 0 10px 30px rgba(0,0,0,.18);
  }
  .card__art {
    position: absolute; inset: 0; width: 100%; height: 100%;
  }
  .brand {
    position: absolute; left: 70px; top: 118px;
    color: var(--navy); font-weight: 700;
  }
  .brand__mark {
    width: 64px; height: 64px; border-radius: 50%;
    background: var(--navy); margin-bottom: 18px; margin-left: 4px;
  }
  .brand__name { font-size: 52px; line-height: 1.05; letter-spacing: -0.5px; }
  .brand__legal { font-size: 37px; line-height: 1.25; }
  .person {
    position: absolute; left: 72px; top: 352px;
  }
  .person__name { color: var(--navy); font-size: 41px; font-weight: 500; line-height: 1.1; }
  .person__title { color: var(--muted); font-size: 25px; line-height: 1.1; }
  .contact {
    position: absolute; left: 75px; top: 460px;
    list-style: none;
  }
  .contact__item {
    display: flex; align-items: center; gap: 17px;
    height: 43px; color: var(--ink); font-size: 29px; font-weight: 500;
  }
  .contact__icon { width: 29px; height: 32px; flex: none; }
</style>
</head>
<body>
  <section class="card" aria-label="Heron Property Inspections business card">
    <svg class="card__art" viewBox="0 0 940 535" preserveAspectRatio="none" aria-hidden="true">
      <path d="M758,0 C832,95 850,265 752,535 L940,535 L940,0 Z" fill="var(--navy)"/>
      <path d="M568,535 C705,492 822,400 836,250 C834,385 792,470 740,535 Z" fill="var(--sky)"/>
    </svg>

    <div class="brand">
      <div class="brand__mark"></div>
      <div class="brand__name">Tim MarlowHeron</div>
      <div class="brand__legal">Property Inspections, LLC</div>
    </div>

    <div class="person">
      <div class="person__name">Employee Name</div>
      <div class="person__title">Managing Director</div>
    </div>

    <ul class="contact">
      <li class="contact__item">
        <svg class="contact__icon" viewBox="0 0 29 32" aria-label="Phone">
          <rect width="29" height="32" fill="var(--navy)"/>
          <rect x="10" y="6" width="10" height="20" rx="1.5" fill="none" stroke="#fff" stroke-width="2"/>
          <line x1="13" y1="22" x2="17" y2="22" stroke="#fff" stroke-width="2"/>
        </svg>
        703-555-0192
      </li>
      <li class="contact__item">
        <svg class="contact__icon" viewBox="0 0 29 32" aria-label="Email">
          <rect width="29" height="32" fill="var(--navy)"/>
          <rect x="5" y="10" width="19" height="13" fill="none" stroke="#fff" stroke-width="2"/>
          <polyline points="5,10 14.5,18 24,10" fill="none" stroke="#fff" stroke-width="2"/>
        </svg>
        tkmarlow@postvale.net
      </li>
      <li class="contact__item">
        <svg class="contact__icon" viewBox="0 0 29 32" aria-label="Address">
          <rect width="29" height="32" fill="var(--navy)"/>
          <path d="M14.5,25 C9,18 8,15 8,13 A6.5,6.5 0 0 1 21,13 C21,15 20,18 14.5,25 Z" fill="none" stroke="#fff" stroke-width="2"/>
          <circle cx="14.5" cy="13" r="2.2" fill="#fff"/>
        </svg>
        7182 Quarry LaneFernhill, Virginia 20148
      </li>
    </ul>
  </section>
</body>
</html>
```